Harbor Crestline (Business Card Design)

Need business cards designed. Something modern, chic, and sleek. Mabye the back of the card should be the navy blue that is in the logo and then just the logo on the back.

Target Market(s)

Those in the hotel, office, and renovation industry

Contact Information for Business Card

1. Logo 2. Dorian Fenwick 3. CEO/Founder 4. Phone: (833) HarbCre / (833) 427-2731 5. Email: dorian@theharborcrestline.com 6. Website: www.theharborcrestline.com

Font styles to use
Other font styles liked:
• Look at the logo font and base the font for everything else off of that.

Colors
0054AA
0677BA
7BADD7
CADEEF
E8F1F8

Requirements
Must have
• Colors that are associated in the logo
Nice to have
• Sleek modern clean and chic design.

```html
<!DOCTYPE html>
<html lang="en">
<head>
<meta charset="utf-8">
<title>Harbor Crestline — Business Card</title>
<link rel="stylesheet" href="https://fonts.googleapis.com/css2?family=Montserrat:wght@500;600&family=Poppins:wght@400;500;700&display=swap">
<style>
  :root {
    --page-bg: #f4f4f4;
    --navy-deep: #080d26;
    --navy-mid: #0a1650;
    --navy-glow: #0c1d66;
    --white: #ffffff;
    --gold: #c9a24a;
    --card-shadow: rgba(0, 0, 0, 0.28);
  }
  * { box-sizing: border-box; margin: 0; padding: 0; }
  html, body {
    width: 684px;
    height: 1200px;
    overflow: hidden;
    background: var(--page-bg);
  }
  .sheet {
    width: 684px;
    height: 1200px;
    display: flex;
    flex-direction: column;
    align-items: center;
    justify-content: center;
    gap: 64px;
  }
  .card {
    position: relative;
    width: 580px;
    height: 331px;
    background:
      radial-gradient(ellipse 60% 70% at 50% 50%, var(--navy-glow) 0%, var(--navy-mid) 45%, var(--navy-deep) 100%);
    box-shadow: 0 10px 28px var(--card-shadow);
    overflow: hidden;
  }

  /* Front */
  .card-front {
    display: flex;
    align-items: center;
    justify-content: center;
  }
  .brand {
    display: flex;
    flex-direction: column;
    align-items: center;
    gap: 18px;
  }
  .brand-mark {
    width: 12px;
    height: 12px;
    background: var(--gold);
    transform: rotate(45deg);
  }
  .brand-name {
    font-family: "Montserrat", sans-serif;
    font-weight: 500;
    font-size: 34px;
    letter-spacing: 3px;
    text-transform: uppercase;
    color: var(--white);
  }

  /* Back */
  .card-back .identity {
    position: absolute;
    left: 28px;
    top: 0;
    width: 212px;
    height: 100%;
    display: flex;
    flex-direction: column;
    align-items: center;
    justify-content: center;
    gap: 14px;
    text-align: center;
  }
  .card-back .identity .brand-name {
    font-size: 22px;
    letter-spacing: 2px;
    line-height: 1.3;
  }
  .divider {
    position: absolute;
    left: 261px;
    top: 72px;
    width: 1.5px;
    height: 164px;
    background: var(--white);
  }
  .contact {
    position: absolute;
    left: 289px;
    top: 82px;
    font-family: "Poppins", sans-serif;
    color: var(--white);
  }
  .person-name {
    font-weight: 700;
    font-size: 25px;
    line-height: 1;
    letter-spacing: 0.3px;
    text-transform: uppercase;
  }
  .person-name .surname { color: var(--gold); }
  .person-role {
    margin-top: 4px;
    font-size: 12.5px;
    color: var(--gold);
  }
  .contact-list {
    list-style: none;
    margin-top: 16px;
    display: flex;
    flex-direction: column;
    gap: 5px;
  }
  .contact-list .phone { font-size: 13.5px; }
  .contact-list .web { font-size: 11.5px; font-weight: 500; }
</style>
</head>
<body>
  <main class="sheet">
    <section class="card card-front" aria-label="Business card front">
      <div class="brand">
        <span class="brand-mark" aria-hidden="true"></span>
        <span class="brand-name">Harbor Crestline</span>
      </div>
    </section>

    <section class="card card-back" aria-label="Business card back">
      <div class="identity">
        <span class="brand-mark" aria-hidden="true"></span>
        <span class="brand-name">Harbor<br>Crestline</span>
      </div>
      <span class="divider" aria-hidden="true"></span>
      <div class="contact">
        <h1 class="person-name">Dorian <span class="surname">Fenwick</span></h1>
        <p class="person-role">CEO/Founder</p>
        <ul class="contact-list">
          <li class="phone">(833) HarbCre</li>
          <li class="phone">(833) 427-2731</li>
          <li class="web">dorian@theharborcrestline.com</li>
          <li class="web">www.theharborcrestline.com</li>
        </ul>
      </div>
    </section>
  </main>
</body>
</html>
```